Vantiqo custom business card design

Need a authentic, innovative business card design for a new mobile app business. I am uploading a few screen images from our app for you to view. I would like app design theme to match business card design. I can also send logo images.

```html
<!DOCTYPE html>
<html lang="en">
<head>
<meta charset="UTF-8">
<title>Vantiqo Business Card</title>
<link rel="stylesheet" href="https://fonts.googleapis.com/css2?family=Roboto:wght@400;500;700&display=swap">
<style>
  :root {
    --backdrop: #dcdcdc;
    --card-white: #ffffff;
    --brand-purple: #6a0096;
    --brand-purple-deep: #62008e;
    --ink-dark: #2b2b2b;
    --ink-muted: #555555;
    --paper-text: #ffffff;
  }
  * { margin: 0; padding: 0; box-sizing: border-box; }
  html, body {
    width: 1200px;
    height: 1200px;
    overflow: hidden;
    background: var(--backdrop);
    font-family: "Roboto", Arial, sans-serif;
  }
  .canvas {
    position: relative;
    width: 1200px;
    height: 1200px;
  }
  .card {
    position: absolute;
    left: 262px;
    width: 686px;
    height: 392px;
  }
  .card-front {
    top: 165px;
    background: var(--card-white);
  }
  .card-back {
    top: 653px;
    background: linear-gradient(180deg, var(--brand-purple) 0%, var(--brand-purple-deep) 100%);
  }

  /* Front */
  .brand-lockup {
    position: absolute;
    left: 492px;
    top: 38px;
    width: 140px;
    display: flex;
    flex-direction: column;
    align-items: center;
  }
  .brand-dot {
    width: 128px;
    height: 128px;
    border-radius: 50%;
    background: var(--brand-purple);
  }
  .brand-name {
    margin-top: 14px;
    font-weight: 700;
    font-size: 38px;
    line-height: 1;
    color: var(--ink-dark);
    letter-spacing: 0.5px;
  }
  .contact-block {
    position: absolute;
    left: 38px;
    top: 286px;
  }
  .person-line {
    display: flex;
    align-items: baseline;
    white-space: nowrap;
  }
  .person-name {
    font-weight: 500;
    font-size: 26px;
    color: var(--brand-purple);
  }
  .person-title {
    font-weight: 400;
    font-size: 17px;
    color: var(--ink-dark);
    margin-left: 6px;
  }
  .contact-line {
    font-size: 16.5px;
    color: var(--ink-muted);
    line-height: 24px;
    white-space: nowrap;
  }
  .person-line + .contact-line { margin-top: 8px; }

  /* Back */
  .back-mark {
    position: absolute;
    left: 241px;
    top: 93px;
    width: 204px;
    height: 204px;
    border-radius: 50%;
    background: var(--paper-text);
    display: flex;
    align-items: center;
    justify-content: center;
  }
  .back-mark-name {
    font-weight: 700;
    font-size: 38px;
    color: var(--brand-purple);
  }
  .back-url {
    position: absolute;
    left: 0;
    right: 0;
    top: 334px;
    text-align: center;
    font-size: 17px;
    letter-spacing: 11px;
    color: var(--paper-text);
  }
</style>
</head>
<body>
  <main class="canvas">
    <section class="card card-front">
      <div class="brand-lockup">
        <div class="brand-dot"></div>
        <div class="brand-name">Vantiqo</div>
      </div>
      <div class="contact-block">
        <div class="person-line">
          <span class="person-name">DANIEL REYES -</span>
          <span class="person-title">CEO/FOUNDER</span>
        </div>
        <p class="contact-line">4120 Harbor View Road, Juneau, Alaska 99801</p>
        <p class="contact-line">P. 555 210 4873 E. daniel@vantiqo.com W. www.vantiqo.com</p>
      </div>
    </section>

    <section class="card card-back">
      <div class="back-mark">
        <span class="back-mark-name">Vantiqo</span>
      </div>
      <p class="back-url">www.vantiqo.com</p>
    </section>
  </main>
</body>
</html>
```